The Quiet Harbor Podcast Cover Art

I'm upgrading my podcast cover art to a new design. The show is called The Quiet Harbor and we interview guests who have gone through different challenges/adversities that we face in life. During the interview, we unpack how they've gotten past the adversity and how that insight might help others. I will link the show and old cover art. I will upload a new photo or two that can be used for the new cover art.

Look at previous cover for items that needed on the cover like Lyrabox, tunewell etc.

Should also have a small caption that states
“UNTOLD STORIES OF EVERYDAY ADVERSITY & PERSEVERANCE”

Tunewell: https://play.tunewellaudio.net/show/8PR4n2GbtqWxLoHvFNZCa7?si=qe3Lx8WbVm-D52KrPhtzRa

Target Market(s)

Podcast learning community

Industry/Entity Type

Podcast, Education

Colors
EB3D1F
EC4F4E
F09395
F8D3D4
FCEDEE

Requirements
Must have
• RM Logo, Colors are red, black and white.

```html
<!DOCTYPE html>
<html lang="en">
<head>
<meta charset="utf-8">
<title>The Quiet Harbor Podcast Cover Art</title>
<link rel="stylesheet" href="https://fonts.googleapis.com/css2?family=Montserrat:wght@500;600;800&display=swap">
<style>
  :root {
    --brand-red: #c8161e;
    --deep-red: #8b2a30;
    --charcoal: #4a4848;
    --white: #ffffff;
    --dot-grey: #b8a9aa;
    --photo-dark: #1e1c1d;
    --photo-mid: #5a5657;
    --photo-light: #a9a6a6;
  }
  html, body {
    margin: 0;
    padding: 0;
    overflow: hidden;
    background: var(--white);
  }
  .cover {
    position: relative;
    width: 1200px;
    height: 1200px;
    overflow: hidden;
    background: linear-gradient(208deg, var(--charcoal) 8%, var(--deep-red) 48%, var(--brand-red) 88%);
    font-family: "Montserrat", Arial, sans-serif;
  }
  .cover-art {
    position: absolute;
    inset: 0;
  }
  .tagline {
    font-family: "Montserrat", Arial, sans-serif;
    font-weight: 800;
    font-size: 72px;
    fill: var(--white);
  }
  .show-name {
    font-family: "Montserrat", Arial, sans-serif;
    font-weight: 600;
    font-size: 30px;
    letter-spacing: 2px;
    fill: var(--white);
  }
  .host-name {
    font-family: "Montserrat", Arial, sans-serif;
    font-weight: 600;
    font-size: 26px;
    letter-spacing: 2px;
    fill: var(--white);
  }
  .slide-dot { fill: var(--dot-grey); }
  .edition-code {
    font-family: "Montserrat", Arial, sans-serif;
    font-weight: 500;
    font-size: 16px;
    fill: var(--white);
  }
</style>
</head>
<body>
<main class="cover">
  <svg class="cover-art" width="1200" height="1200" viewBox="0 0 1200 1200" xmlns="http://www.w3.org/2000/svg">
    <defs>
      <radialGradient id="hostPhotoTone" cx="0.42" cy="0.45" r="0.65">
        <stop offset="0" stop-color="var(--photo-light)"/>
        <stop offset="0.45" stop-color="var(--photo-mid)"/>
        <stop offset="1" stop-color="var(--photo-dark)"/>
      </radialGradient>
    </defs>

    <!-- host photo circle -->
    <circle class="photo-halo" cx="341" cy="338" r="492" fill="#ffffff" opacity="0.18"/>
    <circle class="host-photo" cx="341" cy="338" r="470" fill="url(#hostPhotoTone)" stroke="#ffffff" stroke-width="14"
            role="img" aria-label="Photo of the podcast host smiling at a desk with headphones, a microphone and a laptop"/>

    <!-- show name mark -->
    <text class="show-name" x="1116" y="130" text-anchor="end">
      <tspan x="1116">THE QUIET</tspan>
      <tspan x="1116" dy="40">HARBOR</tspan>
    </text>

    <!-- tagline, read bottom to top -->
    <g class="tagline-block">
      <text class="tagline" transform="translate(769 1125) rotate(-90)" textLength="281" lengthAdjust="spacingAndGlyphs">UNTOLD</text>
      <text class="tagline" transform="translate(881 1125) rotate(-90)" textLength="488" lengthAdjust="spacingAndGlyphs">STORIES OF</text>
      <text class="tagline" transform="translate(988 1125) rotate(-90)" textLength="760" lengthAdjust="spacingAndGlyphs">EVERYDAY ADVERSITY</text>
      <text class="tagline" transform="translate(1116 1125) rotate(-90)" textLength="741" lengthAdjust="spacingAndGlyphs">&amp; PERSEVERANCE</text>
    </g>

    <!-- host mark -->
    <text class="host-name" x="84" y="1110">RAY MARLOW</text>

    <!-- pagination dots -->
    <g class="slide-dots">
      <circle class="slide-dot" cx="351" cy="1052" r="9"/>
      <circle class="slide-dot" cx="410" cy="1052" r="9"/>
      <circle class="slide-dot" cx="470" cy="1052" r="9"/>
      <circle class="slide-dot" cx="530" cy="1052" r="9"/>
      <circle class="slide-dot" cx="592" cy="1052" r="9"/>
    </g>

    <text class="edition-code" x="1148" y="1162">C45</text>
  </svg>
</main>
</body>
</html>
```